Postcard Design

We are a small Jewelry store in Vermont and carry high end Estate Jewelry. We are trying to promote 3 rings we took in recently. I have attached pictures and would like to send text as well for each ring with pricing. We would like two images of each and colorful background but classy. I am also sending our logo, address and contact info which must go on the card. We would like the finish on the front to be glossy if possible. Please let me know what else may be needed to complete this project as quickly as possible. The text is as follows: 1. Platinum 3-stone Diamond ring with 4.61ct Round Brilliant center J VVS2 and two Round brilliant side Diamonds 2.72ctw I-J VVS2-VS1 KRL Certified and Value is $175,000.00 Special Price $125,000.00 2. 18k yellow gold and Platinum ring with 5.50ct Emerald in the center and 1.22ctw in trillion cut diamonds on the sides G-H SI1 Certified value $32,620.00 Special price $25,000.00 3. 18k white gold ring with gorgeous cushion cut Sapphire 5.40ct and .55ctw accent diamonds G-H SI1-2 Retail Value $18,000.00 Special price $12,500.00 Our contact information as follows: Our Logo which I atttached, address: 48 Birchmont Rd. Woodstock VT 05238 Phone: 802-639-4275

```html
<!DOCTYPE html>
<html lang="en">
<head>
<meta charset="utf-8">
<title>Estate Ring Postcard</title>
<link href="https://fonts.googleapis.com/css2?family=Crimson+Pro:ital,wght@0,400;0,600;1,400;1,600&display=swap" rel="stylesheet">
<style>
  :root {
    --ink: #3a3a3a;
    --blue: #2b2fe0;
    --label-blue: #4a5ad8;
    --navy: #1c1f5c;
    --bg-top: #f6f3ff;
    --bg-mid: #eef1fb;
    --bg-end: #f8f1e6;
    --photo-dark: #0c0f12;
  }
  html, body { margin: 0; padding: 0; overflow: hidden; background: var(--bg-mid); }
  .card {
    position: relative;
    width: 1200px;
    height: 930px;
    background: linear-gradient(135deg, var(--bg-top) 0%, var(--bg-mid) 55%, var(--bg-end) 100%);
    font-family: "Crimson Pro", Georgia, serif;
    color: var(--ink);
    overflow: hidden;
  }
  .brand {
    position: absolute;
    left: 73px;
    top: 72px;
    width: 210px;
    font-size: 25px;
    line-height: 27px;
    color: var(--blue);
  }
  .contact {
    position: absolute;
    left: 309px;
    top: 78px;
    font-size: 18px;
    letter-spacing: 2.4px;
    line-height: 25px;
  }
  .photo {
    position: absolute;
    top: 162px;
    width: 180px;
    height: 120px;
    display: flex;
    gap: 4px;
  }
  .photo-1 { left: 76px; }
  .photo-2 { left: 281px; }
  .photo-3 { left: 486px; }
  .view { flex: 1; }
  .photo-1 .view { background: radial-gradient(ellipse at 50% 40%, #3a4248, var(--photo-dark) 70%); }
  .photo-2 .view { background: radial-gradient(ellipse at 50% 40%, #5a5a22, var(--photo-dark) 70%); }
  .photo-3 .view { background: radial-gradient(ellipse at 50% 35%, #24308a, var(--photo-dark) 70%); }
  .photo-num {
    position: absolute;
    left: 13px;
    bottom: 6px;
    font-size: 20px;
    font-weight: 600;
    color: var(--label-blue);
  }
  .offer {
    position: absolute;
    left: 76px;
    width: 600px;
    font-size: 22px;
    line-height: 25px;
  }
  .offer-1 { top: 368px; }
  .offer-2 { top: 509px; }
  .offer-3 { top: 654px; }
  .offer p { margin: 0; }
  .offer-num { color: var(--label-blue); font-weight: 600; }
  .price { margin-top: 6px !important; font-style: italic; font-size: 21px; }
  .price-value { font-weight: 600; margin-right: 10px; }
  .price-special { color: var(--blue); }
  .rule {
    position: absolute;
    left: 712px;
    width: 455px;
    border-top: 1.5px solid var(--blue);
  }
  .rule-1 { top: 415px; }
  .rule-2 { top: 480px; }
  .rule-3 { top: 549px; border-top-color: var(--navy); }
  .rule-4 { top: 616px; }
</style>
</head>
<body>
<div class="card">
  <div class="brand">Hollis Reed<br>Estate Jewelers</div>
  <div class="contact">
    <div>48 Birchmont Rd. Woodstock, VT 05238</div>
    <div>Phone: 802-639-4275</div>
  </div>

  <div class="photo photo-1">
    <div class="view" role="img" aria-label="Platinum three-stone diamond ring, front view"></div>
    <div class="view" role="img" aria-label="Platinum three-stone diamond ring, side view"></div>
    <span class="photo-num">1.</span>
  </div>
  <div class="photo photo-2">
    <div class="view" role="img" aria-label="Yellow gold and platinum emerald ring, front view"></div>
    <div class="view" role="img" aria-label="Yellow gold and platinum emerald ring, side view"></div>
    <span class="photo-num">2.</span>
  </div>
  <div class="photo photo-3">
    <div class="view" role="img" aria-label="White gold sapphire ring, front view"></div>
    <div class="view" role="img" aria-label="White gold sapphire ring, side view"></div>
    <span class="photo-num">3.</span>
  </div>

  <div class="offer offer-1">
    <p><span class="offer-num">1.</span> Platinum 3-stone Diamond ring with 4.61ct round brilliant<br>center J VVS2 and two round brilliant side Diamonds. 2.72ctw<br>I-J VVS2-VS1 KRL Certified.</p>
    <p class="price"><span class="price-value">Value: $175,000.00</span> <span class="price-special">Special Price $125,000.00</span></p>
  </div>

  <div class="offer offer-2">
    <p><span class="offer-num">2.</span> 18k yellow Gold and Platinum ring with 5.50ct Emerald in<br>the center and 1.22ctw in trillion cut diamonds on the sides.<br>G-H SI1 Certified.</p>
    <p class="price"><span class="price-value">Value: $32,620.00</span> <span class="price-special">Special Price $25,000.00</span></p>
  </div>

  <div class="offer offer-3">
    <p><span class="offer-num">3.</span> 18k White Gold ring with gorgeous cushion cut Sapphire<br>5.40ct and .55ctw accent diamonds. G-H SI1-2 Certified.</p>
    <p class="price"><span class="price-value">Value: $18,000.00</span> <span class="price-special">Special Price $12,500.00</span></p>
  </div>

  <div class="rule rule-1"></div>
  <div class="rule rule-2"></div>
  <div class="rule rule-3"></div>
  <div class="rule rule-4"></div>
</div>
</body>
</html>
```